Whitcombe Business Card Design

The name of the business is Dario Whitcombe, CPA LLC
The service that we offer is Accounting, Tax & Consulting Services. I need it to have the following items:
Dario Whitcombe, Principal
Phone Number
Email Address
Physical Address

I have attached the company logo, one in black and one in white. Please provide a design in black background and the other in white background. Please include "Accounting, Tax & Consulting Services". I want the business card to be clean and very professional.

```html
<!DOCTYPE html>
<html lang="en">
<head>
<meta charset="utf-8">
<title>Dario Whitcombe, CPA LLC — Business Cards</title>
<link href="https://fonts.googleapis.com/css2?family=Montserrat:wght@400;500;600;700&display=swap" rel="stylesheet">
<style>
  :root {
    --backdrop: #3b3b3d;
    --card-black: #1f1f21;
    --card-black-2: #2b2b2e;
    --card-white: #ffffff;
    --ink: #2f2f31;
    --grey: #8a8a8c;
    --red: #9b1c1c;
    --white: #ffffff;
  }
  * { box-sizing: border-box; margin: 0; padding: 0; }
  html, body { width: 1200px; height: 1095px; overflow: hidden; }
  body {
    background: var(--backdrop);
    font-family: "Montserrat", Arial, sans-serif;
    position: relative;
  }
  .card {
    position: absolute;
    width: 700px;
    height: 400px;
    overflow: hidden;
  }

  /* Front: black card */
  .card--front { left: 80px; top: 70px; background: var(--card-black); }
  .card__texture {
    position: absolute; inset: 0;
    background: radial-gradient(ellipse at 30% 60%, var(--card-black-2) 0%, var(--card-black) 70%);
  }
  .brand--front {
    position: absolute; left: 110px; top: 168px;
    display: flex; align-items: center; gap: 22px;
  }
  .brand__mark {
    width: 64px; height: 64px; flex: none;
    border: 6px solid var(--white);
  }
  .brand__name {
    font-weight: 600; font-size: 24px; letter-spacing: 0.4px;
    text-transform: uppercase; color: var(--white); line-height: 1;
    white-space: nowrap;
  }
  .brand__tagline {
    margin-top: 10px;
    font-weight: 600; font-size: 16px; letter-spacing: 2.4px;
    text-transform: uppercase; color: var(--grey); white-space: nowrap;
  }

  /* Back: white card */
  .card--back { left: 420px; top: 620px; background: var(--card-white); }
  .brand--back {
    position: absolute; left: 24px; top: 96px; width: 336px;
    display: flex; flex-direction: column; align-items: center; gap: 18px;
  }
  .brand--back .brand__mark { border-color: var(--ink); width: 56px; height: 56px; }
  .brand--back .brand__name { color: var(--ink); font-size: 18px; text-align: center; }
  .brand--back .brand__tagline { font-size: 11.5px; letter-spacing: 1.9px; margin-top: 7px; text-align: center; }

  .divider {
    position: absolute; left: 378px; top: 56px;
    width: 1.5px; height: 190px; background: var(--ink);
  }
  .contact { position: absolute; left: 400px; top: 50px; width: 290px; }
  .contact__name {
    font-weight: 600; font-size: 24px; color: var(--ink);
    text-transform: uppercase; letter-spacing: 0.3px; white-space: nowrap;
  }
  .contact__role { font-size: 15px; color: var(--red); margin: 3px 0 14px 4px; }
  .contact__list { list-style: none; margin-left: 6px; }
  .contact__item {
    display: flex; align-items: center; gap: 9px;
    font-size: 14px; color: var(--ink); letter-spacing: 0.4px; margin-bottom: 8px;
    white-space: nowrap;
  }
  .contact__icon { width: 13px; height: 13px; fill: var(--red); flex: none; }

  .services-band {
    position: absolute; left: 0; right: 0; top: 298px; height: 52px;
    background: var(--red);
    display: flex; align-items: center; justify-content: center;
    color: var(--white); font-weight: 600; font-size: 19px; letter-spacing: 1px;
    text-transform: uppercase;
  }
</style>
</head>
<body>

  <section class="card card--front" aria-label="Business card front">
    <div class="card__texture" role="img" aria-label="Subtle dark tonal background texture"></div>
    <div class="brand brand--front">
      <span class="brand__mark"></span>
      <div>
        <p class="brand__name">Dario Whitcombe, CPA, LLC</p>
        <p class="brand__tagline">Certified Public Accountant</p>
      </div>
    </div>
  </section>

  <section class="card card--back" aria-label="Business card back">
    <div class="brand brand--back">
      <span class="brand__mark"></span>
      <div>
        <p class="brand__name">Dario Whitcombe, CPA, LLC</p>
        <p class="brand__tagline">Certified Public Accountant</p>
      </div>
    </div>

    <div class="divider"></div>

    <div class="contact">
      <p class="contact__name">Dario Whitcombe</p>
      <p class="contact__role">Principal</p>
      <ul class="contact__list">
        <li class="contact__item">
          <svg class="contact__icon" viewBox="0 0 24 24"><path d="M6.6 10.8a15.1 15.1 0 0 0 6.6 6.6l2.2-2.2a1 1 0 0 1 1-.25 11.4 11.4 0 0 0 3.6.57 1 1 0 0 1 1 1V20a1 1 0 0 1-1 1A17 17 0 0 1 3 4a1 1 0 0 1 1-1h3.5a1 1 0 0 1 1 1c0 1.25.2 2.45.57 3.57a1 1 0 0 1-.25 1z"/></svg>
          (855) 410-2276
        </li>
        <li class="contact__item">
          <svg class="contact__icon" viewBox="0 0 24 24"><path d="M2 5h20v14H2z M2 5l10 8 10-8" stroke="#fff" stroke-width="1.5"/></svg>
          info@whitcombecpa.com
        </li>
        <li class="contact__item">
          <svg class="contact__icon" viewBox="0 0 24 24"><circle cx="12" cy="12" r="10"/><path d="M2 12h20M12 2c3 3 3 17 0 20M12 2c-3 3-3 17 0 20" stroke="#fff" stroke-width="1.3" fill="none"/></svg>
          www.whitcombecpa.com
        </li>
        <li class="contact__item">
          <svg class="contact__icon" viewBox="0 0 24 24"><path d="M12 2a7 7 0 0 0-7 7c0 5.2 7 13 7 13s7-7.8 7-13a7 7 0 0 0-7-7zm0 9.5A2.5 2.5 0 1 1 12 6.5a2.5 2.5 0 0 1 0 5z"/></svg>
          214 Larkin St, Austin, TX 78701
        </li>
      </ul>
    </div>

    <div class="services-band">Accounting, Tax &amp; Consulting Services</div>
  </section>

</body>
</html>
```